Vehicle wrap

Hurricane storm shutters supply and install need to have business address phone number website and a scan URL

Brindlewaygatepanels.com

Target Market(s)

residential and commercial

Colors
EB3D1F
EC4F4E
F09395
F8D3D4
FCEDEE

Requirements
Must have
• a red emblem next to our logo
Nice to have
• pictures of a house with hurricane shutters

```html
<!DOCTYPE html>
<html lang="en">
<head>
<meta charset="utf-8">
<title>Brindleway Gate Panels – Vehicle Wrap Side</title>
<link rel="stylesheet" href="https://fonts.googleapis.com/css2?family=Bebas+Neue&family=Montserrat:wght@300;400;600;700&display=swap">
<style>
  :root {
    --backdrop: #6c82a1;
    --wrap-white: #e4e4e4;
    --wrap-black: #121212;
    --wrap-red: #d52a2a;
    --ink: #111111;
    --paper: #ffffff;
    --photo-sky: #9fc3dd;
    --photo-roof: #b28a6a;
    --photo-lawn: #5f8a4a;
  }
  * { margin: 0; padding: 0; box-sizing: border-box; }
  html, body { width: 1200px; height: 611px; overflow: hidden; }
  body { background: var(--backdrop); position: relative; font-family: "Montserrat", sans-serif; }

  .wrap-panel { position: absolute; left: 60px; top: 150px; width: 1080px; height: 310px; }
  .wrap-panel svg.wrap-art { position: absolute; inset: 0; width: 1080px; height: 310px; }

  .address {
    position: absolute; right: 800px; top: 118px;
    color: var(--paper); font-weight: 600; font-size: 13px; line-height: 16px;
    text-align: right; letter-spacing: .3px; white-space: nowrap;
  }

  .brand { position: absolute; left: 302px; top: 142px; display: flex; align-items: center; gap: 16px; }
  .brand-mark { width: 74px; height: 74px; border-radius: 50%; background: var(--wrap-red); flex: none; }
  .brand-name {
    font-family: "Bebas Neue", sans-serif; color: var(--ink);
    font-size: 46px; line-height: 40px; letter-spacing: .5px; white-space: nowrap;
  }

  .website {
    position: absolute; left: 300px; top: 268px;
    color: var(--paper); font-weight: 300; font-size: 16px; letter-spacing: 5.4px;
    white-space: nowrap;
  }

  .contact { position: absolute; right: 26px; top: 100px; width: 200px; color: var(--paper); text-align: right; }
  .phone { font-family: "Bebas Neue", sans-serif; font-size: 28px; line-height: 28px; display: flex; justify-content: flex-end; align-items: center; gap: 8px; letter-spacing: .5px; }
  .phone svg { width: 15px; height: 15px; fill: var(--paper); }
  .contact hr { border: 0; border-top: 1px solid var(--paper); margin: 4px 0 6px; }
  .service { font-weight: 700; font-size: 15.5px; line-height: 18px; white-space: nowrap; }
  .service-note { font-size: 6.6px; line-height: 10px; white-space: nowrap; letter-spacing: .2px; }
  .tagline { margin-top: 10px; font-size: 9.6px; line-height: 10.5px; letter-spacing: .3px; }
</style>
</head>
<body>
  <section class="wrap-panel">
    <svg class="wrap-art" viewBox="0 0 1080 310" xmlns="http://www.w3.org/2000/svg">
      <defs>
        <linearGradient id="photo-tones" x1="0" y1="0" x2="0" y2="1">
          <stop offset="0" stop-color="var(--photo-sky)"/>
          <stop offset=".45" stop-color="var(--photo-roof)"/>
          <stop offset=".75" stop-color="#8a8a86"/>
          <stop offset="1" stop-color="var(--photo-lawn)"/>
        </linearGradient>
      </defs>
      <rect class="base" x="0" y="0" width="1080" height="310" rx="14" fill="var(--wrap-white)"/>
      <polygon class="roof-band" points="520,0 760,0 745,28 540,28" fill="var(--wrap-red)"/>
      <polygon class="front-block" points="0,100 300,100 190,310 0,310" fill="var(--wrap-black)"/>
      <polygon class="front-accent" points="262,170 300,170 270,222 232,222" fill="var(--wrap-red)"/>
      <polygon class="website-band" points="300,250 760,250 740,300 280,300" fill="var(--wrap-black)"/>
      <polygon class="photo-accent" points="630,100 690,100 655,140" fill="var(--wrap-red)"/>
      <polygon class="house-photo" role="img" aria-label="Photo of a single-storey house with closed hurricane shutters and palm trees"
        points="695,100 915,100 810,300 600,300 640,230" fill="url(#photo-tones)"/>
      <polygon class="rear-block" points="915,100 1080,100 1080,310 800,310 810,300" fill="var(--wrap-black)"/>
      <polygon class="rear-accent" points="1055,225 1080,225 1080,300 1020,300" fill="var(--wrap-red)"/>
    </svg>

    <p class="address">2207 Fernhollow<br>St, Orlando, FL 32801</p>

    <div class="brand">
      <span class="brand-mark"></span>
      <span class="brand-name">Brindleway<br>Gate Panels</span>
    </div>

    <p class="website">brindlewaygatepanels.com</p>

    <div class="contact">
      <p class="phone">
        <svg viewBox="0 0 24 24" aria-hidden="true"><path d="M6.6 10.8a15.1 15.1 0 0 0 6.6 6.6l2.2-2.2a1 1 0 0 1 1-.25 11.4 11.4 0 0 0 3.6.57 1 1 0 0 1 1 1V20a1 1 0 0 1-1 1A17 17 0 0 1 3 4a1 1 0 0 1 1-1h3.5a1 1 0 0 1 1 1c0 1.25.2 2.45.57 3.57a1 1 0 0 1-.25 1z"/></svg>
        321-555-0148
      </p>
      <hr>
      <p class="service">Security Systems</p>
      <p class="service-note">For Business, Commercial or Residential</p>
      <hr>
      <p class="tagline">Protect Your Home<br>and Protect Your<br>Family with<br>Storm Shutters</p>
    </div>
  </section>
</body>
</html>
```